Business card for a new cabinet shop company named Veloran Cabinets for high end cabinets

Design a business card, thinking dark rich green with colours to speak of high end luxury ie; cream, gold, black possibly

Mitchell Tarrowby
Director Craftsman
Email: info@veloranjoinery-example.com.au
Instagram : @veloran.cabinets

```html
<!DOCTYPE html>
<html lang="en">
<head>
<meta charset="utf-8">
<title>Veloran Cabinets – Business Card</title>
<link rel="stylesheet" href="https://fonts.googleapis.com/css2?family=Poppins:wght@700&family=Open+Sans:wght@400&display=swap">
<style>
  :root {
    --ink: #04110b;
    --stone: #123325;
    --stone-light: #1a4231;
    --forest: #1c3d2e;
    --forest-deep: #0f281d;
    --white: #ffffff;
    --cream: #f3ead2;
    --gold: #e3b63f;
    --gold-light: #f6d77a;
    --gold-deep: #a8721e;
  }
  html, body {
    margin: 0;
    padding: 0;
    width: 1200px;
    height: 686px;
    overflow: hidden;
    background: var(--ink);
  }
  .card {
    position: relative;
    width: 1200px;
    height: 686px;
    overflow: hidden;
    background: var(--ink);
  }
  .card__marble {
    position: absolute;
    inset: 0;
    background:
      radial-gradient(ellipse at 30% 35%, var(--stone-light) 0%, rgba(18,51,37,0) 55%),
      radial-gradient(ellipse at 75% 70%, var(--stone) 0%, rgba(4,17,11,0) 50%),
      linear-gradient(135deg, var(--stone) 0%, var(--ink) 60%, var(--forest-deep) 100%);
  }
  .card__swooshes {
    position: absolute;
    inset: 0;
    width: 1200px;
    height: 686px;
  }
  .card__content {
    position: absolute;
    inset: 0;
    text-align: center;
  }
  .card__name {
    position: absolute;
    left: 0;
    right: 0;
    top: 172px;
    margin: 0;
    font-family: "Poppins", sans-serif;
    font-weight: 700;
    font-size: 64px;
    line-height: 1;
    letter-spacing: 0.5px;
    color: var(--white);
    text-transform: uppercase;
  }
  .card__title {
    position: absolute;
    left: 0;
    right: 0;
    top: 248px;
    margin: 0;
    font-family: "Open Sans", sans-serif;
    font-weight: 400;
    font-size: 45px;
    line-height: 1;
    color: var(--gold);
  }
  .card__divider {
    position: absolute;
    left: 399px;
    top: 321px;
    width: 402px;
    height: 10px;
  }
  .card__contact {
    position: absolute;
    left: 0;
    right: 0;
    margin: 0;
    font-family: "Open Sans", sans-serif;
    font-weight: 400;
    line-height: 1;
    color: var(--white);
  }
  .card__email { top: 364px; font-size: 50px; }
  .card__handle { top: 452px; font-size: 62px; }
</style>
</head>
<body>
  <div class="card">
    <div class="card__marble" role="img" aria-label="Dark green marble texture with soft veining"></div>

    <svg class="card__swooshes" viewBox="0 0 1050 600" preserveAspectRatio="none" aria-hidden="true">
      <defs>
        <linearGradient id="goldSweep" x1="0" y1="0" x2="1" y2="1">
          <stop offset="0" stop-color="var(--gold-deep)"/>
          <stop offset="0.45" stop-color="var(--gold-light)"/>
          <stop offset="0.75" stop-color="var(--gold)"/>
          <stop offset="1" stop-color="var(--gold-deep)"/>
        </linearGradient>
      </defs>
      <!-- top right sweep -->
      <path d="M700,0 C800,20 960,110 1050,230 L1050,0 Z" fill="var(--forest)"/>
      <path d="M455,0 C720,30 950,130 1050,300 L1050,230 C960,110 800,20 700,0 Z" fill="url(#goldSweep)"/>
      <path d="M850,0 C950,30 1020,80 1050,125" fill="none" stroke="url(#goldSweep)" stroke-width="4"/>
      <!-- bottom left sweep -->
      <path d="M0,110 C60,300 250,520 560,600 L0,600 Z" fill="var(--forest)"/>
      <path d="M0,240 C100,430 300,560 520,600" fill="none" stroke="url(#goldSweep)" stroke-width="3"/>
      <path d="M0,330 C120,480 280,570 430,600 L300,600 C180,560 60,480 0,420 Z" fill="url(#goldSweep)"/>
      <path d="M0,470 C70,540 150,580 220,600 L0,600 Z" fill="var(--forest-deep)"/>
    </svg>

    <div class="card__content">
      <h1 class="card__name">Mitchell Tarrowby</h1>
      <p class="card__title">Director Craftsman</p>
      <svg class="card__divider" viewBox="0 0 402 10" role="img" aria-label="Thin gold ornamental divider">
        <rect x="0" y="4" width="402" height="2" fill="var(--gold)"/>
      </svg>
      <p class="card__contact card__email">info@veloranjoinery-example.com.au</p>
      <p class="card__contact card__handle">@veloran.cabinets</p>
    </div>
  </div>
</body>
</html>
```